Heron Loan Partners Business Card

We need a business card design for our mortgage servicing company. In addition to servicing the loans of homeowners, we help homeowners with purchasing their homes and any mortgage refinancing. We would like to see designs that use the colors in the logo attached below (gold-ish yellow and navy blue), and any other design you deem fit! The design should communicate a simpler life with smart mortgages provided by Heron.

```html
<!DOCTYPE html>
<html lang="en">
<head>
<meta charset="utf-8">
<title>Heron Loan Partners Business Card</title>
<link rel="stylesheet" href="https://fonts.googleapis.com/css2?family=Open+Sans:wght@400;600;700&display=swap">
<style>
  :root {
    --stage: #222222;
    --paper: #f4f4f4;
    --paper-back: #ffffff;
    --gold: #d9aa3c;
    --navy: #221c52;
    --ink: #111111;
  }
  * { box-sizing: border-box; margin: 0; padding: 0; }
  html, body { width: 1200px; height: 780px; overflow: hidden; }
  body {
    background: var(--stage);
    font-family: "Open Sans", Arial, sans-serif;
    position: relative;
  }
  .card {
    position: absolute;
    top: 241px;
    width: 520px;
    height: 297px;
    overflow: hidden;
  }
  .card--front { left: 60px; background: var(--paper); }
  .card--back { left: 620px; background: var(--paper-back); display: flex; align-items: center; justify-content: center; }

  .card__wave { position: absolute; inset: 0; width: 100%; height: 100%; }

  .brand {
    display: flex;
    align-items: center;
    gap: 8px;
    color: var(--navy);
    font-weight: 700;
    line-height: 1.05;
  }
  .brand__dot { width: 12px; height: 12px; border-radius: 50%; background: var(--gold); flex: none; }
  .brand--small { position: absolute; left: 40px; top: 58px; font-size: 20px; width: 190px; }
  .brand--large { font-size: 38px; }

  .divider {
    position: absolute;
    left: 244px;
    top: 62px;
    width: 1.5px;
    height: 168px;
    background: var(--ink);
  }

  .details { position: absolute; left: 264px; top: 66px; color: var(--ink); }
  .details__name { font-size: 22px; font-weight: 700; line-height: 1.1; }
  .details__first { color: var(--gold); }
  .details__last { color: var(--navy); }
  .details__title { font-size: 12px; margin-top: 4px; }
  .details__address { font-size: 12px; line-height: 1.45; margin-top: 10px; }
  .contact { list-style: none; margin-top: 6px; font-size: 12px; line-height: 1.45; }
  .contact__item { display: flex; align-items: center; gap: 6px; }
  .contact__icon { width: 11px; height: 11px; fill: var(--gold); flex: none; }
</style>
</head>
<body>

  <section class="card card--front" aria-label="Business card front">
    <svg class="card__wave" viewBox="0 0 520 297" preserveAspectRatio="none" aria-hidden="true">
      <path d="M0 220 C 70 226, 130 250, 260 275 C 360 292, 440 296, 520 297 L 0 297 Z" fill="var(--gold)"/>
      <path d="M118 238 C 220 268, 340 284, 520 290 L 520 297 C 360 292, 230 278, 118 238 Z" fill="var(--navy)"/>
    </svg>

    <div class="brand brand--small">
      <span class="brand__dot"></span>
      <span class="brand__name">Heron Loan Partners</span>
    </div>

    <div class="divider"></div>

    <div class="details">
      <p class="details__name"><span class="details__first">Dana</span> <span class="details__last">Whitfield</span></p>
      <p class="details__title">Managing Director</p>
      <p class="details__address">1840 Lakeside Ave. Suite 300<br>Riverton, TX 75011</p>
      <ul class="contact">
        <li class="contact__item">
          <svg class="contact__icon" viewBox="0 0 24 24"><path d="M6.6 10.8a15.1 15.1 0 0 0 6.6 6.6l2.2-2.2c.3-.3.7-.4 1-.2 1.1.4 2.3.6 3.6.6.6 0 1 .4 1 1V20c0 .6-.4 1-1 1A17 17 0 0 1 3 4c0-.6.4-1 1-1h3.5c.6 0 1 .4 1 1 0 1.3.2 2.5.6 3.6.1.3 0 .7-.2 1z"/></svg>
          (555) 214-6038
        </li>
        <li class="contact__item">
          <svg class="contact__icon" viewBox="0 0 24 24"><path d="M2 5h20v14H2z M4 7v.4l8 5 8-5V7l-8 5z" fill-rule="evenodd"/></svg>
          info@heronloans.com
        </li>
        <li class="contact__item">
          <svg class="contact__icon" viewBox="0 0 24 24"><circle cx="12" cy="12" r="10"/></svg>
          www.heronloans.com
        </li>
      </ul>
    </div>
  </section>

  <section class="card card--back" aria-label="Business card back">
    <div class="brand brand--large">
      <span class="brand__dot"></span>
      <span class="brand__name">Heron Loan Partners</span>
    </div>
  </section>

</body>
</html>
```